VORTEQ

It’s is a startup business. We design and build new products.

Target Market(s)

For my first two products, they are targeting the laundry market, hanger accessory, and new modern style clothes dryer. I also have a Pet Treat product at patent stage, and there are other products not yet started but will be more engineering based. Therefore from young adults to older population

Industry/Entity Type

Colours of website to match the logo (att)

Coding

Coded - Design and coding required

Number of Pages Required

1 page

Font styles to use
Other font styles liked:
• Some of the same font as the logo

Colors

Designer to choose colors to be used in the design.

Requirements
Must have
• An upbeat vibe - the logo looks great so inline with that !
Should not have
• anything old fashioned and old style fonts

```html
<!DOCTYPE html>
<html lang="en">
<head>
<meta charset="utf-8">
<title>VORTEQ – Innovation &amp; Technical Services</title>
<link href="https://fonts.googleapis.com/css2?family=Michroma&family=Roboto:wght@400;500;700&family=Roboto+Condensed:wght@400;700&display=swap" rel="stylesheet">
<style>
:root{
  --teal:#12b8c8;
  --teal-deep:#0a9fb8;
  --blue:#1b8fd2;
  --accent:#1aa6d6;
  --ink:#1f1f24;
  --muted:#444;
  --hero-bg:#f3f4f5;
  --soft-blue:#e9f7fb;
  --footer-top:#5b5fb4;
  --footer-bot:#2f3a8c;
  --footer-bar:#29358a;
  --white:#fff;
}
*{margin:0;padding:0;box-sizing:border-box}
html,body{width:1200px;height:3600px;overflow:hidden}
body{position:relative;background:var(--white);font-family:"Roboto",Arial,sans-serif;color:var(--ink)}
.abs{position:absolute}
.display{font-family:"Michroma",sans-serif;letter-spacing:3px;text-transform:uppercase;color:var(--ink)}
.btn-outline{position:absolute;display:flex;align-items:center;justify-content:center;border:2px solid var(--accent);border-radius:30px;color:var(--accent);font-weight:700;font-size:15px;background:var(--white)}
.photo{position:absolute;overflow:hidden}

/* header */
.brand{left:143px;top:30px;font-family:"Michroma",sans-serif;font-size:26px;color:var(--blue);display:flex;align-items:center;gap:10px}
.brand .mark{width:18px;height:18px;border-radius:50%;background:var(--teal)}
.nav{left:463px;top:35px;display:flex;gap:27px;font-size:15px;color:var(--ink)}
.nav .active{color:var(--accent);position:relative}
.nav .active::before{content:"";position:absolute;left:50%;top:-14px;width:8px;height:8px;margin-left:-4px;border-radius:50%;background:var(--accent)}
.login{left:843px;top:35px;font-size:15px;font-weight:700;color:var(--teal-deep);text-decoration:underline}

/* hero */
.hero-title{left:143px;top:205px;font-size:52px;letter-spacing:6px}
.hero-text{left:143px;top:282px;width:380px;font-size:14px;font-weight:500;line-height:20px}
.hero-dots span{position:absolute;left:1116px;width:10px;height:10px;border-radius:50%;background:#dadde0}
.hero-dots span.on{background:var(--accent)}

/* about */
.about-title{left:625px;top:810px;font-size:29px}
.about-text{left:625px;top:857px;width:432px;font-size:13px;line-height:22.3px;color:#333;text-align:justify}
.icon-badge{position:absolute;width:84px;height:84px;border-radius:50%;display:flex;align-items:center;justify-content:center}
.framed{border:5px solid var(--white);border-radius:30px;box-shadow:0 6px 20px rgba(0,0,0,.18)}

/* services */
.section-title{left:0;width:1200px;text-align:center;font-size:29px}
.service-card{position:absolute;top:1420px;width:437px;height:450px;background:var(--white);border-radius:32px;box-shadow:0 10px 30px rgba(0,70,110,.08)}
.service-card .photo{left:34px;top:25px;width:370px;height:313px;border-radius:26px}
.service-card .label{position:absolute;left:34px;top:353px;width:370px;height:67px;border:2.5px solid var(--teal-deep);border-radius:14px;display:flex;align-items:center;justify-content:center;color:var(--teal-deep);font-weight:700;font-size:20px}

/* products */
.product-card{position:absolute;top:2103px;width:284px;height:375px;background:var(--white);text-align:center}
.product-card .photo{left:32px;top:18px;width:220px;height:220px;border-radius:50%;border:5px solid var(--white);box-shadow:0 0 0 2px #e6f4f7}
.product-card h3{position:absolute;left:0;top:258px;width:100%;font-size:20px;font-weight:700}
.product-card p{position:absolute;left:0;top:296px;width:100%;font-size:16px;line-height:24px;color:#333}
.arrow{position:absolute;top:2276px}

/* contact */
.cta-title{left:0;top:2818px;width:1200px;text-align:center;font-size:24px;line-height:36px;letter-spacing:4px}

/* footer */
.foot-h{font-size:20px;font-weight:700;color:var(--white);line-height:28px}
.newsletter{left:143px;top:3340px;width:271px;height:42px;border:1px solid rgba(255,255,255,.7);color:var(--white);font-size:13px;padding:13px 16px}
.social{position:absolute;top:3403px;width:28px;height:28px;border-radius:50%;background:var(--white)}
.contact-item{position:absolute;left:503px;font-family:"Roboto Condensed",sans-serif;color:var(--white)}
.contact-item b{display:block;font-size:15px;margin-bottom:4px;padding-left:42px}
.contact-item span{display:block;font-size:12px;padding-left:42px}
.contact-item svg{position:absolute;left:0;top:0}
.qlinks{position:absolute;top:3325px;font-family:"Roboto Condensed",sans-serif;color:var(--white);font-size:15px;list-style:none}
.qlinks li{height:32px;padding-left:24px;position:relative}
.qlinks li::before{content:"»";position:absolute;left:0;top:-2px;font-size:16px}
.copy{left:0;top:3553px;width:1200px;text-align:center;color:var(--white);font-family:"Roboto Condensed",sans-serif;font-size:15px}
</style>
</head>
<body>

<!-- background bands -->
<svg class="abs" style="left:0;top:0" width="1200" height="3600" aria-hidden="true">
  <defs>
    <linearGradient id="gTeal" x1="0" x2="1" y1="0" y2="0">
      <stop offset="0" stop-color="#13c0cf"/><stop offset=".5" stop-color="#1b9fd4"/><stop offset="1" stop-color="#12b8b8"/>
    </linearGradient>
    <linearGradient id="gProd" x1="0" x2="0" y1="0" y2="1">
      <stop offset="0" stop-color="#10cbd6"/><stop offset="1" stop-color="#1799d2"/>
    </linearGradient>
    <linearGradient id="gSoft" x1="0" x2="0" y1="0" y2="1">
      <stop offset="0" stop-color="#ffffff"/><stop offset="1" stop-color="#e6f6fb"/>
    </linearGradient>
    <linearGradient id="gFoot" x1="0" x2="0" y1="0" y2="1">
      <stop offset="0" stop-color="#5b5fb4"/><stop offset="1" stop-color="#2f3a8c"/>
    </linearGradient>
  </defs>
  <rect x="0" y="0" width="1200" height="700" fill="#f3f4f5"/>
  <path d="M0 660 Q600 420 1200 640 L1200 900 L0 900 Z" fill="url(#gTeal)"/>
  <path d="M0 830 Q600 410 1200 830 L1200 1220 L0 1220 Z" fill="#fff"/>
  <rect x="0" y="1220" width="1200" height="600" fill="url(#gSoft)"/>
  <path d="M0 1215 Q600 1150 1200 1215 L1200 1300 L0 1300 Z" fill="#fff"/>
  <path d="M0 1818 L1200 1818 L1200 2540 Q600 2760 0 2540 Z" fill="url(#gProd)"/>
  <path d="M0 2900 Q200 3080 600 3180 Q1000 3080 1200 2900 L1200 3600 L0 3600 Z" fill="url(#gTeal)"/>
  <path d="M0 3060 Q600 3270 1200 3060 L1200 3600 L0 3600 Z" fill="url(#gFoot)"/>
  <path d="M0 2900 Q600 3360 1200 2900 L1200 2880 L0 2880 Z" fill="#fff"/>
  <path d="M0 2880 Q150 3020 600 3180 Q1050 3020 1200 2880 Z" fill="#fff"/>
  <rect x="0" y="3522" width="1200" height="78" fill="#29358a"/>
</svg>

<!-- header -->
<div class="abs brand"><span class="mark"></span>VORTEQ</div>
<nav class="abs nav"><span class="active">Home</span><span>About</span><span>Services</span><span>Blog</span><span>Contact</span></nav>
<div class="abs login">&#9679; Login</div>
<div class="btn-outline" style="left:925px;top:25px;width:130px;height:38px">Get A Quote</div>

<!-- hero -->
<h1 class="abs display hero-title">VORTEQ</h1>
<p class="abs hero-text">Lorem ipsum dolor sit amet, consectetur adipiscing elit, sed do eiusmod tempor incididunt ut labore</p>
<div class="btn-outline" style="left:143px;top:335px;width:130px;height:37px">Get A Quote</div>
<div class="photo" role="img" aria-label="Smiling businessman in white shirt and tie holding a laptop" style="left:620px;top:70px;width:460px;height:500px;border-radius:200px 200px 0 0;background:radial-gradient(ellipse at 50% 35%,#e9e6e2 0,#d7d9dc 55%,#f3f4f5 100%)"></div>
<div class="hero-dots"><span class="on" style="top:233px"></span><span style="top:277px"></span><span style="top:321px"></span><span style="top:365px"></span></div>

<!-- about -->
<div class="abs" style="left:315px;top:805px;width:190px;height:190px;border-radius:50%;background:#0e9fb0"></div>
<div class="photo framed" role="img" aria-label="Team working at computers in a dark office" style="left:175px;top:722px;width:197px;height:196px;background:linear-gradient(135deg,#2c4f7a,#6fa4c9 60%,#1d2f4e)"></div>
<div class="photo framed" role="img" aria-label="Colleagues meeting around a table with laptops" style="left:385px;top:837px;width:195px;height:196px;background:linear-gradient(135deg,#4a4a48,#a7a9a3 55%,#6b6d6a)"></div>
<div class="photo framed" role="img" aria-label="Young man examining a prototype part" style="left:175px;top:935px;width:197px;height:196px;background:linear-gradient(135deg,#b9b3a8,#e4d7c2 50%,#8a8f87)"></div>
<div class="icon-badge" style="left:620px;top:715px;background:#e3f5fa">
  <svg width="44" height="44" viewBox="0 0 44 44" fill="none" stroke="#12a0c0" stroke-width="2"><circle cx="22" cy="17" r="10"/><circle cx="22" cy="17" r="4"/><path d="M17 27v6h10v-6M18 37h8M22 2v3M8 8l2 2M36 8l-2 2M4 17h3M37 17h3"/></svg>
</div>
<h2 class="abs display about-title">About VORTEQ</h2>
<p class="abs about-text">Lorem ipsum dolor sit amet, consectetur adipiscing elit, sed do eiusmod tempor incididunt ut labore et dolore magna aliqua. Ut enim ad minim veniam, quis nostrud exercitation ullamco laboris nisi ut aliquip ex ea commodo consequat. Duis aute irure dolor in reprehenderit in voluptate velit esse cillum dolore eu fugiat nulla pariatur. Excepteur sint occaecat cupidatat non proident, sunt in culpa qui officia deserunt mollit anim id est laborum. Lorem ipsum dolor sit amet, consectetur adipiscing elit, sed do eiusmod tempor incididunt ut labore et dolore magna aliqua. Lorem ipsum dolor sit amet, consectetur adipiscing elit, sed do eiusmod tempor incididunt ut labore et dolore magna aliqua.</p>
<div class="btn-outline" style="left:625px;top:1098px;width:130px;height:37px">Learn More &#10148;</div>

<!-- services -->
<div class="icon-badge" style="left:558px;top:1245px;background:#fff">
  <svg width="44" height="44" viewBox="0 0 44 44" fill="none" stroke="#12a0c0" stroke-width="2"><circle cx="17" cy="15" r="6"/><circle cx="29" cy="15" r="4"/><path d="M6 32c6-4 10-4 16-2l10-4c3 0 3 3 1 4l-11 6c-6 2-10 0-16-2"/></svg>
</div>
<h2 class="abs display section-title" style="top:1348px">Our Services Areas</h2>
<div class="service-card" style="left:143px">
  <div class="photo" role="img" aria-label="Woman inspecting washing machines in an appliance store" style="background:linear-gradient(135deg,#ccc9c3,#f0ede8 45%,#a8a49d)"></div>
  <div class="label">Laundry Market</div>
</div>
<div class="service-card" style="left:620px">
  <div class="photo" role="img" aria-label="Man feeding treats to two dogs indoors" style="background:linear-gradient(135deg,#8a6a4c,#d9d3ca 55%,#5b7a4e)"></div>
  <div class="label">Pet Treat Product</div>
</div>

<!-- products -->
<div class="icon-badge" style="left:558px;top:1935px;background:#fff">
  <svg width="44" height="44" viewBox="0 0 44 44" fill="none" stroke="#12a0c0" stroke-width="2"><path d="M8 20l14-6 14 6v14l-14 6-14-6z M8 20l14 6 14-6 M22 26v14"/><path d="M17 10l4 4 7-8"/></svg>
</div>
<h2 class="abs display section-title" style="top:2038px;color:#fff">Our Products</h2>
<svg class="arrow" style="left:55px" width="34" height="34" viewBox="0 0 34 34" fill="none" stroke="#fff" stroke-width="3"><path d="M30 17H5M15 7L5 17l10 10"/></svg>
<svg class="arrow" style="left:1106px" width="34" height="34" viewBox="0 0 34 34" fill="none" stroke="#fff" stroke-width="3"><path d="M4 17h25M19 7l10 10-10 10"/></svg>
<div class="product-card" style="left:143px;background:linear-gradient(90deg,#dff7fa,#fff 60%)">
  <div class="photo" role="img" aria-label="Man loading clothes into a front-loading dryer" style="background:linear-gradient(135deg,#c9c2b8,#eeeae4 50%,#7f7a72)"></div>
  <h3>Laundry Innovations</h3>
  <p>Hanger Accessory<br>Modern Clothes Dryer</p>
</div>
<div class="product-card" style="left:457px">
  <div class="photo" role="img" aria-label="Small dog sitting on a rug beside a pet toy" style="background:linear-gradient(180deg,#4e5a4a,#a6957c 55%,#caa879)"></div>
  <h3>Pet Innovations</h3>
  <p>Patent-Pending Pet<br>Treat Product</p>
</div>
<div class="product-card" style="left:771px;background:linear-gradient(270deg,#dff7fa,#fff 60%)">
  <div class="photo" role="img" aria-label="Hand holding a glowing light bulb" style="background:radial-gradient(circle at 50% 40%,#ffe8b8,#d9b78d 45%,#8d7a68)"></div>
  <h3>Future Products</h3>
  <p>Teasing upcoming<br>engineering-driven solutions.</p>
</div>

<!-- contact -->
<div class="icon-badge" style="left:558px;top:2717px;background:#e3f5fa">
  <svg width="44" height="44" viewBox="0 0 44 44" fill="none" stroke="#12a0c0" stroke-width="2"><rect x="16" y="8" width="22" height="16" rx="2"/><path d="M16 9l11 8 11-8"/><path d="M8 14c-2 8 6 20 16 22l4-5-5-4-3 2c-3-2-5-5-6-8l2-3-4-5z"/></svg>
</div>
<h2 class="abs display cta-title">Have a question or interested in<br>collaborating?<br>Get in touch with us today!</h2>
<div class="btn-outline" style="left:535px;top:2947px;width:130px;height:37px">Contact Us</div>

<!-- footer -->
<div class="abs foot-h" style="left:143px;top:3270px">SUBSCRIBE TO<br>OUR NEWSLETTER</div>
<div class="abs newsletter">Email address</div>
<svg class="abs" style="left:390px;top:3352px" width="16" height="16" viewBox="0 0 16 16" fill="#fff"><path d="M15 1L1 7l5 2 2 6z"/></svg>
<span class="social" aria-label="Social profile" style="left:144px"></span>
<span class="social" aria-label="Social profile" style="left:177px;background:#1aa6d6"></span>
<span class="social" aria-label="Social profile" style="left:209px"></span>

<div class="abs foot-h" style="left:503px;top:3270px">CONTACT INFO</div>
<div class="contact-item" style="top:3327px">
  <svg width="16" height="20" viewBox="0 0 16 20" fill="#fff"><path d="M8 0a7 7 0 0 0-7 7c0 5 7 13 7 13s7-8 7-13a7 7 0 0 0-7-7zm0 10a3 3 0 1 1 0-6 3 3 0 0 1 0 6z"/></svg>
  <b>Address</b><span>Lorem ipsum dolor sit amet</span>
</div>
<div class="contact-item" style="top:3382px">
  <svg width="20" height="16" viewBox="0 0 20 16" fill="#fff"><path d="M0 2h20v12H0z"/><path d="M0 2l10 7 10-7" stroke="#3f4a9a" fill="none" stroke-width="1.5"/></svg>
  <b>Email</b><span>info@companyname.com</span>
</div>
<div class="contact-item" style="top:3442px">
  <svg width="18" height="18" viewBox="0 0 18 18" fill="#fff"><path d="M3 1l4 4-2 2c1 3 3 5 6 6l2-2 4 4-3 3C7 18 0 11 0 4z"/></svg>
  <b>Phone</b><span>+1 888 888 8888</span>
</div>

<div class="abs foot-h" style="left:765px;top:3270px">QUICK LINKS</div>
<ul class="qlinks" style="left:765px"><li>Home</li><li>About</li><li>Services</li><li>Contact</li></ul>
<ul class="qlinks" style="left:901px"><li>Terms and Condition</li><li>Privacy policy</li><li>Help</li><li>Support</li></ul>

<p class="abs copy">&copy; Copyrights 2025 | All Rights Reserved</p>

</body>
</html>
```